Maple Bus Card

i own a building in the bronx ny - its called "Maple 7 on 2 HDFC"i want a classy logo / business card - nothing too religuous but it is like a family there - its a large apartment building - colors i like dark red, black, medium shade of gray also reg business card stuff tel # 555-201-0173 address 4738 Larkwell Ave Ashcombe NY 12987 Email fijosh@aol.comslogan - " Together under one roof "i can send u a picture of the building for the backside

```html
<!DOCTYPE html>
<html lang="en">
<head>
<meta charset="utf-8">
<title>Maple 7 on 2 HDFC — Business Card</title>
<link href="https://fonts.googleapis.com/css2?family=Nunito+Sans:wght@400;800&display=swap" rel="stylesheet">
<style>
  :root {
    --backdrop: #d9d9d9;
    --card-white: #f7f6f3;
    --brand-red: #a51c24;
    --brick-red: #a8161f;
    --brick-dark: #7e1117;
    --ink: #2b2b2b;
    --muted: #555555;
    --gold: #b8902f;
  }
  * { box-sizing: border-box; margin: 0; padding: 0; }
  html, body { width: 1200px; height: 1200px; overflow: hidden; }
  body {
    background: var(--backdrop);
    font-family: "Nunito Sans", sans-serif;
    position: relative;
  }
  .card {
    position: absolute;
    left: 180px;
    width: 840px;
    height: 480px;
    box-shadow: 0 6px 18px rgba(0,0,0,0.18);
    overflow: hidden;
  }
  .card--front { top: 90px; background: var(--card-white); }
  .card--back { top: 630px; }

  .brand {
    position: absolute;
    left: 50px;
    top: 180px;
    width: 340px;
    text-align: center;
  }
  .brand__name {
    font-weight: 800;
    color: var(--brand-red);
    font-size: 30px;
    line-height: 1.15;
  }
  .brand__slogan {
    margin-top: 10px;
    font-size: 15px;
    color: var(--muted);
    letter-spacing: 0.3px;
  }

  .divider {
    position: absolute;
    left: 410px;
    top: 95px;
    width: 3px;
    height: 260px;
    background: var(--gold);
    transform: skewX(-4deg);
  }

  .contact {
    position: absolute;
    left: 480px;
    top: 115px;
    width: 340px;
  }
  .contact__name {
    font-weight: 800;
    font-size: 30px;
    color: var(--ink);
    text-transform: uppercase;
    line-height: 1.1;
  }
  .contact__position {
    font-size: 22px;
    color: var(--brand-red);
    text-transform: uppercase;
    margin-bottom: 26px;
  }
  .contact__row {
    display: flex;
    align-items: flex-start;
    gap: 16px;
    font-size: 22px;
    color: var(--ink);
    line-height: 1.25;
    margin-bottom: 8px;
  }
  .contact__icon { width: 20px; height: 22px; flex: none; margin-top: 3px; }

  .gold-band {
    position: absolute;
    left: 0;
    right: 0;
    top: 432px;
    height: 28px;
    background: var(--gold);
  }

  .building-art {
    width: 100%;
    height: 100%;
    background: linear-gradient(180deg, var(--brick-red) 0%, var(--brick-dark) 100%);
  }
</style>
</head>
<body>
  <section class="card card--front">
    <div class="brand">
      <h1 class="brand__name">Maple 7 on 2 HDFC</h1>
      <p class="brand__slogan">Together under one roof</p>
    </div>

    <div class="divider" aria-hidden="true"></div>

    <div class="contact">
      <p class="contact__name">Your Name</p>
      <p class="contact__position">Position</p>

      <div class="contact__row">
        <svg class="contact__icon" viewBox="0 0 24 24" aria-hidden="true">
          <path fill="var(--brand-red)" d="M6.6 10.8a15 15 0 0 0 6.6 6.6l2.2-2.2c.3-.3.7-.4 1-.2 1.1.4 2.3.6 3.6.6.6 0 1 .4 1 1V20c0 .6-.4 1-1 1C10.6 21 3 13.4 3 4c0-.6.4-1 1-1h3.5c.6 0 1 .4 1 1 0 1.3.2 2.5.6 3.6.1.3 0 .7-.2 1z"/>
        </svg>
        <span>555-201-0173</span>
      </div>
      <div class="contact__row">
        <svg class="contact__icon" viewBox="0 0 24 24" aria-hidden="true">
          <rect x="2" y="5" width="20" height="14" fill="none" stroke="var(--brand-red)" stroke-width="2"/>
          <path d="M2 5l10 8 10-8M2 19l7-7M22 19l-7-7" fill="none" stroke="var(--brand-red)" stroke-width="1.6"/>
        </svg>
        <span>mavreld@quintmail.com</span>
      </div>
      <div class="contact__row">
        <svg class="contact__icon" viewBox="0 0 24 24" aria-hidden="true">
          <path fill="var(--brand-red)" d="M12 2a7 7 0 0 0-7 7c0 5 7 13 7 13s7-8 7-13a7 7 0 0 0-7-7zm0 9.5a2.5 2.5 0 1 1 0-5 2.5 2.5 0 0 1 0 5z"/>
        </svg>
        <span>4738 Larkwell Ave,<br>Ashcombe NY 12987</span>
      </div>
    </div>

    <div class="gold-band"></div>
  </section>

  <section class="card card--back">
    <div class="building-art" role="img" aria-label="Illustration of the red brick apartment building entrance with columns, a gold-glass door and a name sign above it"></div>
  </section>
</body>
</html>
```